Velvet Lantern rebranding my business with a new business card

I have my new logo and now I need a refresher on my business cards. I really want something fun and fresh. I like black background or anything to make the color pop.
Logo
Name: Velvet Lantern
Contact Info as stated below:
Mira Pellow
555-013-4762
Logo
Name: Velvet Lantern
Mira Pellow
555-013-4762
fb.me/VelvetLanternbyMira
Instagram: @VelvetLanternbyMira

Industry/Entity Type

Business

Contact Information for Business Card

double-sided. Logo on one side. Contact info on the other.

Requirements
Must have
• Logo
• Name: Velvet Lantern
• Contact Info as stated below:
• Mira Pellow
• 555-013-4762
• fb.me/VelvetLanternbyMira
• fb.me/VelvetLanternbyMira

```html
<!DOCTYPE html>
<html lang="en">
<head>
<meta charset="utf-8">
<title>Velvet Lantern — Business Card</title>
<link href="https://fonts.googleapis.com/css2?family=Delius&display=swap" rel="stylesheet">
<style>
  :root {
    --bg: #e4e4e4;
    --card-pink: #f6c3c7;
    --card-pink-soft: #f8d3d5;
    --ring-pink: #ee9aa6;
    --ring-dark: #2b2226;
    --white: #ffffff;
    --teal: #5cc4b3;
    --ink: #2a2a2a;
    --brand-ink: #3a2a2e;
  }
  * { margin: 0; padding: 0; box-sizing: border-box; }
  html, body { width: 1200px; height: 576px; overflow: hidden; }
  body {
    background: var(--bg);
    font-family: "Delius", sans-serif;
    color: var(--ink);
    position: relative;
  }
  .card {
    position: absolute;
    border-radius: 14px;
    overflow: hidden;
    box-shadow: 0 3px 8px rgba(0,0,0,0.25);
  }
  .card-front {
    left: 82px; top: 138px; width: 484px; height: 294px;
    background: var(--card-pink);
  }
  .logo-badge {
    position: absolute;
    left: 138px; top: 44px; width: 208px; height: 208px;
    border-radius: 50%;
    background: var(--white);
    border: 2px solid var(--ring-dark);
    box-shadow: inset 0 0 0 5px var(--white), inset 0 0 0 7px var(--ring-pink);
    display: flex; align-items: center; justify-content: center;
  }
  .brand-name {
    font-family: "Delius", sans-serif;
    color: var(--brand-ink);
    font-size: 26px;
    text-align: center;
    line-height: 1.15;
  }
  .card-back {
    left: 602px; top: 138px; width: 480px; height: 292px;
    background: var(--card-pink-soft);
  }
  .card-back .wave { position: absolute; inset: 0; }
  .holder-name {
    position: absolute; left: 28px; top: 52px;
    font-size: 24px; color: var(--ink);
  }
  .holder-title {
    position: absolute; left: 29px; top: 88px;
    font-size: 11px; color: var(--ink);
  }
  .contact {
    position: absolute; left: 26px; top: 210px;
    list-style: none; font-size: 16px; color: var(--ink);
  }
  .contact li { display: flex; align-items: center; gap: 8px; height: 25px; }
  .contact-icon { width: 17px; height: 17px; flex: none; }
  .brand-block {
    position: absolute; left: 275px; top: 0; width: 205px; height: 292px;
    display: flex; align-items: center; justify-content: center;
  }
  .brand-block .brand-name { font-size: 30px; }
</style>
</head>
<body>

<section class="card card-front" aria-label="Card front">
  <div class="logo-badge">
    <span class="brand-name">Velvet<br>Lantern</span>
  </div>
</section>

<section class="card card-back" aria-label="Card back">
  <svg class="wave" viewBox="0 0 480 292" aria-hidden="true">
    <path d="M204 0 C180 60 190 110 215 160 C240 210 235 260 255 292 L480 292 L480 0 Z" fill="var(--white)"/>
    <path d="M216 0 L238 0 C214 60 224 110 246 160 C268 210 262 260 280 292 L262 292 C244 258 252 212 230 162 C206 110 196 58 216 0 Z" fill="var(--teal)"/>
    <path d="M226 40 C212 80 222 116 238 150" fill="none" stroke="var(--white)" stroke-width="3" stroke-linecap="round"/>
  </svg>

  <h1 class="holder-name">Mira Pellow</h1>
  <p class="holder-title">Managing Director</p>

  <ul class="contact">
    <li>
      <svg class="contact-icon" viewBox="0 0 18 18" aria-hidden="true">
        <rect x="1" y="1" width="16" height="16" rx="3" fill="none" stroke="var(--ink)" stroke-width="1.3"/>
        <path d="M6 4.5 L7.5 4.5 L8.2 6.8 L7.2 7.6 C7.8 9 8.9 10.1 10.3 10.8 L11.1 9.8 L13.4 10.5 L13.4 12 C13.4 12.6 12.9 13 12.3 13 C8.4 12.7 5.3 9.6 5 5.7 C5 5 5.4 4.5 6 4.5 Z" fill="var(--ink)"/>
      </svg>
      555-013-4762
    </li>
    <li>
      <svg class="contact-icon" viewBox="0 0 18 18" aria-hidden="true">
        <rect x="1" y="1" width="16" height="16" rx="3" fill="none" stroke="var(--ink)" stroke-width="1.3"/>
      </svg>
      VelvetLanternbyMira
    </li>
  </ul>

  <div class="brand-block">
    <span class="brand-name">Velvet<br>Lantern</span>
  </div>
</section>

</body>
</html>
```